Low Ferry Guild - Wavering CD Cover

To prepare a CD Cover for the single "Wavering" by Low Ferry Guild.
You can hear the single here:
http://lowferryguild-band.example/listen/

The LFG logo and backdrop are also provided if you want to incorporate them into the CD cover design, though that isn't mandatory.

Song is about deciding on taking on a serious relationship, and leaving the single life behind.

Target Market(s)

Music listeners, 18-50 yrs old, into retro 80s, Marrowmen/Tide Rollers

Industry/Entity Type

Music Download

Requirements
Must have
• LFG logo
• Wavering title
Nice to have
• Use of backdrop, or facimile
Should not have
• Too obvious on the term Wavering

```html
<!DOCTYPE html>
<html lang="en">
<head>
<meta charset="utf-8">
<title>Low Ferry Guild – Wavering</title>
<link rel="stylesheet" href="https://fonts.googleapis.com/css2?family=Antonio:wght@400&family=Raleway:wght@300&display=swap">
<style>
  :root {
    --sky-deep: #1b2356;
    --sky-mid: #4a6aa8;
    --sky-light: #8fa6cf;
    --cloud: #e9d6d6;
    --sun: #fff6e6;
    --edge: #0c0c1e;
    --logo-ink: #1c1a20;
    --title-ink: #f4f1f4;
  }
  html, body {
    margin: 0;
    padding: 0;
    width: 1200px;
    height: 1200px;
    overflow: hidden;
    background: var(--edge);
  }
  .cover {
    position: relative;
    width: 1200px;
    height: 1200px;
    overflow: hidden;
  }
  .cover__backdrop {
    position: absolute;
    inset: 0;
    background:
      radial-gradient(circle at 184px 384px, var(--sun) 0, rgba(255,240,225,0.85) 60px, rgba(240,200,210,0.35) 170px, rgba(240,200,210,0) 320px),
      radial-gradient(ellipse 420px 300px at 900px 240px, rgba(233,214,214,0.75), rgba(233,214,214,0) 100%),
      radial-gradient(ellipse 480px 260px at 760px 900px, rgba(233,214,214,0.7), rgba(233,214,214,0) 100%),
      radial-gradient(ellipse 260px 200px at 120px 1120px, rgba(233,214,214,0.5), rgba(233,214,214,0) 100%),
      radial-gradient(ellipse 760px 760px at 600px 620px, var(--sky-light) 0, var(--sky-mid) 55%, var(--sky-deep) 85%, var(--edge) 100%);
  }
  .band-name {
    position: absolute;
    left: 486px;
    top: 624px;
    width: 226px;
    margin: 0;
    font-family: "Antonio", "Arial Narrow", sans-serif;
    font-weight: 400;
    color: var(--logo-ink);
    text-transform: uppercase;
    text-align: center;
    line-height: 1;
  }
  .band-name__line { display: block; }
  .band-name__line--top { font-size: 160px; letter-spacing: 2px; }
  .band-name__line--mid { font-size: 148px; letter-spacing: 2px; margin-top: -6px; }
  .band-name__line--low { font-size: 97px; letter-spacing: 0; margin-top: 2px; }
  .single-title {
    position: absolute;
    left: 0;
    top: 1080px;
    width: 1200px;
    height: 50px;
  }
  .single-title text {
    font-family: "Raleway", "Helvetica Neue", sans-serif;
    font-weight: 300;
    font-size: 34px;
    fill: var(--title-ink);
  }
</style>
</head>
<body>
  <main class="cover">
    <div class="cover__backdrop" role="img" aria-label="Photograph: silhouette of a person leaping across a gap between two rocky cliffs against a bright blue sky with sunburst and clouds"></div>

    <h1 class="band-name">
      <span class="band-name__line band-name__line--top">Low</span>
      <span class="band-name__line band-name__line--mid">Ferry</span>
      <span class="band-name__line band-name__line--low">Guild</span>
    </h1>

    <svg class="single-title" viewBox="0 0 1200 50" aria-label="Wavering">
      <text x="270" y="38" textLength="660" lengthAdjust="spacing">WAVERING</text>
    </svg>
  </main>
</body>
</html>
```